We need packaging box design for our solar lights

We need a design for our solar string lights packaging boxes. The final design should communicate an added enjoyment, comfort and beauty when our lights are used to light up warm evening nights in places like backyard, patio restaurant or even family event.

Front and back side of box can be more visual while sides can be used for technical information about the product. There are 2 types of boxes which will have same design - except they need to indicate difference in # of bulbs 10 or 16 . also size of 16 bulb product box is slightly larger so design will need to be slightly adjusted.

Our original logo needs to have "Meadowglow Lamps" text added to it as well.

We put all together in the attachment with some of the examples of photos we like.

Below are more attached files:
1st attachment - general info and samples of photos
Second attachments are photos of our product - they can be adjusted/photoshoped in any way you wish to make the design - or any other acceptable photos you create can be used
Third set of attachments are box templates for 10 and 16 bulbs size box
last are files for logo - choose any you like, edit any colors / text needs to be added/changed to "Meadowglow Lamps " - not Meadowglow

Target Market(s)

People with yards, patios, restaurants, wedding places... any celebrations or just relaxing during nice warm evening in the beautifully lit place...

Colors

Designer to choose colors to be used in the design.

Requirements
Must have
• indication of bulb numbers
• logo and name Meadowglow lamps
• rest is up to creativity of designer
Nice to have
• some icons

```html
<!DOCTYPE html>
<html lang="en">
<head>
<meta charset="utf-8">
<title>Meadowglow Lamps – Solar String Lights Box Dieline</title>
<link rel="stylesheet" href="https://fonts.googleapis.com/css2?family=Oswald:wght@600&family=Roboto+Slab:wght@700&family=Open+Sans:wght@600;700&display=swap">
<style>
  :root {
    --paper: #ffffff;
    --edge: #333333;
    --flap: #06066b;
    --panel: #0c1a4d;
    --panel-deep: #081237;
    --gold: #d8c38c;
    --cream: #f4efe4;
    --orange: #f0781e;
    --lime: #9be22d;
    --eco-green: #1ea535;
    --badge-brown: #5a3a12;
    --wave-copper: #b87a5a;
    --wave-slate: #7a86a8;
  }
  html, body { margin: 0; padding: 0; overflow: hidden; background: var(--paper); }
  .dieline { display: block; width: 1200px; height: 679px; }
  .sheet-frame { fill: var(--paper); stroke: var(--edge); stroke-width: 2; }
  .flap { fill: var(--flap); }
  .panel { fill: var(--panel); }
  .brand-title { font-family: "Oswald", sans-serif; font-weight: 600; fill: var(--gold); letter-spacing: 1px; }
  .brand-sub { font-family: "Roboto Slab", serif; font-weight: 700; fill: var(--cream); }
  .brand-mark { font-family: "Open Sans", sans-serif; font-weight: 700; fill: var(--cream); font-size: 7px; letter-spacing: .5px; }
  .feature-list { font-family: "Open Sans", sans-serif; font-weight: 700; fill: var(--orange); font-size: 7.2px; }
  .feature-bullet { fill: var(--orange); }
  .info-head { font-family: "Open Sans", sans-serif; font-weight: 700; fill: var(--lime); font-size: 6.4px; }
  .info-body { font-family: "Open Sans", sans-serif; font-weight: 600; fill: var(--orange); font-size: 5px; }
  .badge-frame { fill: var(--badge-brown); stroke: var(--cream); stroke-width: 1.5; }
  .badge-count { font-family: "Oswald", sans-serif; font-weight: 600; fill: var(--cream); }
  .badge-label { font-family: "Oswald", sans-serif; font-weight: 600; fill: var(--cream); }
  .eco-icon { fill: var(--eco-green); }
  .eco-glyph { fill: var(--paper); }
  .eco-caption { font-family: "Open Sans", sans-serif; font-weight: 600; fill: var(--paper); font-size: 3.6px; }
  .hex-frame { fill: none; stroke: #1c4fd6; stroke-width: 3; }
</style>
</head>
<body>
<svg class="dieline" viewBox="0 0 1368 774" xmlns="http://www.w3.org/2000/svg">
  <defs>
    <linearGradient id="bokeh-tone" x1="0" y1="0" x2="0" y2="1">
      <stop offset="0" stop-color="#1a2350"/>
      <stop offset=".5" stop-color="#3a3a4a"/>
      <stop offset="1" stop-color="#0c1a4d"/>
    </linearGradient>
    <linearGradient id="wave-tone" x1="0" y1="0" x2="0" y2="1">
      <stop offset="0" stop-color="#0c1a4d"/>
      <stop offset=".45" stop-color="#6a7398"/>
      <stop offset=".75" stop-color="#b87a5a"/>
      <stop offset="1" stop-color="#2a2f5e"/>
    </linearGradient>
    <radialGradient id="product-tone" cx=".6" cy=".55" r=".6">
      <stop offset="0" stop-color="#dfe3ee"/>
      <stop offset=".45" stop-color="#4d5a84"/>
      <stop offset="1" stop-color="#0c1a4d"/>
    </radialGradient>
    <linearGradient id="photo-tone" x1="0" y1="0" x2="1" y2="1">
      <stop offset="0" stop-color="#2a2418"/>
      <stop offset=".5" stop-color="#8a6a38"/>
      <stop offset="1" stop-color="#1c1810"/>
    </linearGradient>
  </defs>

  <rect class="sheet-frame" x="1" y="1" width="1366" height="772"/>

  <!-- Top lid (front top) -->
  <g class="lid-top">
    <path class="panel" d="M48 360 V75 Q48 35 88 35 H376 Q416 35 416 75 V360 Z"/>
    <path class="flap" d="M48 75 Q48 35 88 35 H376 Q416 35 416 75 Z"/>
    <rect x="48" y="75" width="368" height="85" fill="url(#bokeh-tone)" role="img" aria-label="Scattered warm bokeh light dots"/>
    <text class="brand-title" x="226" y="205" font-size="36" text-anchor="middle">MEADOWGLOW</text>
    <text class="brand-sub" x="230" y="235" font-size="28" text-anchor="middle">Lamps</text>
    <path d="M48 290 C140 230 230 300 416 245 V360 H48 Z" fill="url(#wave-tone)" role="img" aria-label="Soft flowing light waves"/>
  </g>

  <!-- Glue tab left -->
  <rect class="flap" x="8" y="363" width="40" height="184"/>

  <!-- Front panel -->
  <g class="panel-front">
    <rect class="panel" x="48" y="360" width="368" height="187"/>
    <rect x="200" y="360" width="216" height="187" fill="url(#product-tone)" role="img" aria-label="Solar string light bulbs with solar panel on a stake"/>
    <text class="brand-title" x="140" y="413" font-size="28" text-anchor="middle">MEADOWGLOW</text>
    <text class="brand-sub" x="142" y="441" font-size="24" text-anchor="middle">Lamps</text>
    <circle cx="372" cy="478" r="5" fill="var(--cream)"/>
    <text class="brand-mark" x="372" y="494" text-anchor="middle">MEADOWGLOW</text>
    <g class="bulb-badge">
      <rect class="badge-frame" x="70" y="481" width="46" height="57" rx="8"/>
      <text class="badge-count" x="93" y="510" font-size="22" text-anchor="middle">10</text>
      <text class="badge-label" x="93" y="521" font-size="8" text-anchor="middle">BULBS</text>
      <text class="badge-label" x="93" y="528" font-size="4.5" text-anchor="middle">SOLAR STRING</text>
      <text class="badge-label" x="93" y="534" font-size="4.5" text-anchor="middle">LIGHTS</text>
    </g>
    <g class="eco-icons">
      <circle class="eco-icon" cx="153" cy="522" r="14"/>
      <circle class="eco-glyph" cx="153" cy="518" r="4"/>
      <text class="eco-caption" x="153" y="530" text-anchor="middle">Sun charge</text>
      <circle class="eco-icon" cx="190" cy="522" r="14"/>
      <path class="eco-glyph" d="M192 512 a7 7 0 1 0 4 11 a5.5 5.5 0 1 1 -4 -11 Z"/>
      <text class="eco-caption" x="190" y="530" text-anchor="middle">Auto night</text>
      <circle class="eco-icon" cx="227" cy="522" r="14"/>
      <path class="eco-glyph" d="M227 524 V514 M227 518 q-5 -5 -7 0 q4 3 7 0 M227 516 q5 -5 7 0 q-4 3 -7 0" stroke="var(--paper)" stroke-width="1.2" fill="none"/>
      <text class="eco-caption" x="227" y="530" text-anchor="middle">Eco power</text>
    </g>
  </g>

  <!-- Side panel A -->
  <g class="panel-side-features">
    <path class="flap" d="M420 363 V215 Q420 203 432 203 H648 Q666 203 670 220 L705 363 Z"/>
    <rect class="panel" x="416" y="363" width="289" height="184"/>
    <circle cx="665" cy="388" r="5" fill="var(--cream)"/>
    <text class="brand-mark" x="665" y="409" text-anchor="middle" font-size="6">MEADOWGLOW</text>
    <g class="feature-list">
      <rect class="feature-bullet" x="445" y="395" width="5" height="5"/>
      <text x="457" y="400">10 LED warm white light bulb string</text>
      <rect class="feature-bullet" x="445" y="407" width="5" height="5"/>
      <text x="457" y="412">Waterproof connector for easy installation</text>
      <rect class="feature-bullet" x="445" y="419" width="5" height="5"/>
      <text x="457" y="424">Total length 29.5 ft / Lighted length 19.7 ft  for 16 bulb</text>
      <text x="457" y="436">product )</text>
      <rect class="feature-bullet" x="445" y="443" width="5" height="5"/>
      <text x="457" y="448">Creates pleasant ambient light perfect for Backyard,</text>
      <text x="457" y="460">Patio, Party, Restaurant  Wedding or other scenes</text>
      <rect class="feature-bullet" x="445" y="467" width="5" height="5"/>
      <text x="457" y="472">Safe and Convenient: Solar Powered, no need to worry</text>
      <text x="457" y="484">about the socket location, can be used everywhere</text>
    </g>
    <path d="M416 520 C500 500 600 530 705 515 V547 H416 Z" fill="url(#wave-tone)" role="img" aria-label="Soft flowing light waves"/>
  </g>

  <!-- Back panel -->
  <g class="panel-back">
    <rect class="panel" x="705" y="363" width="368" height="184"/>
    <rect x="705" y="500" width="368" height="47" fill="url(#bokeh-tone)" role="img" aria-label="Scattered warm bokeh light dots"/>
    <text class="brand-title" x="807" y="415" font-size="28" text-anchor="middle">MEADOWGLOW</text>
    <text class="brand-sub" x="810" y="443" font-size="24" text-anchor="middle">Lamps</text>
    <circle cx="1035" cy="388" r="5" fill="var(--cream)"/>
    <text class="brand-mark" x="1035" y="409" text-anchor="middle" font-size="6">MEADOWGLOW</text>
    <g class="eco-icons">
      <circle class="eco-icon" cx="766" cy="481" r="14"/>
      <circle class="eco-glyph" cx="766" cy="477" r="4"/>
      <text class="eco-caption" x="766" y="489" text-anchor="middle">Sun charge</text>
      <circle class="eco-icon" cx="803" cy="481" r="14"/>
      <path class="eco-glyph" d="M805 471 a7 7 0 1 0 4 11 a5.5 5.5 0 1 1 -4 -11 Z"/>
      <text class="eco-caption" x="803" y="489" text-anchor="middle">Auto night</text>
      <circle class="eco-icon" cx="840" cy="481" r="14"/>
      <path d="M840 483 V473 M840 477 q-5 -5 -7 0 q4 3 7 0 M840 475 q5 -5 7 0 q-4 3 -7 0" stroke="var(--paper)" stroke-width="1.2" fill="none"/>
      <text class="eco-caption" x="840" y="489" text-anchor="middle">Eco power</text>
    </g>
    <g class="photo-hexes">
      <polygon points="967,375 1003,396 1003,437 967,458 931,437 931,396" fill="url(#photo-tone)" role="img" aria-label="Patio lit by string lights at dusk"/>
      <polygon class="hex-frame" points="967,375 1003,396 1003,437 967,458 931,437 931,396"/>
      <polygon points="926,445 962,466 962,507 926,528 890,507 890,466" fill="url(#photo-tone)" role="img" aria-label="Garden path with string lights at night"/>
      <polygon class="hex-frame" points="926,445 962,466 962,507 926,528 890,507 890,466"/>
      <polygon points="1008,445 1044,466 1044,507 1008,528 972,507 972,466" fill="url(#photo-tone)" role="img" aria-label="Warm bulbs glowing over a yard"/>
      <polygon class="hex-frame" points="1008,445 1044,466 1044,507 1008,528 972,507 972,466"/>
    </g>
    <g class="bulb-badge">
      <rect class="badge-frame" x="944" y="478" width="46" height="57" rx="8"/>
      <text class="badge-count" x="967" y="507" font-size="22" text-anchor="middle">10</text>
      <text class="badge-label" x="967" y="518" font-size="8" text-anchor="middle">BULBS</text>
      <text class="badge-label" x="967" y="525" font-size="4.5" text-anchor="middle">SOLAR STRING</text>
      <text class="badge-label" x="967" y="531" font-size="4.5" text-anchor="middle">LIGHTS</text>
    </g>
  </g>

  <!-- Side panel B -->
  <g class="panel-side-info">
    <path class="flap" d="M1073 363 L1105 225 Q1110 203 1130 203 H1330 Q1345 203 1345 218 L1358 363 Z"/>
    <rect class="panel" x="1073" y="363" width="285" height="184"/>
    <text class="info-head" x="1107" y="386">How the Solar Light work:</text>
    <text class="info-body" x="1107" y="396">The solar light has a solar panel that converts sunlight into electricity which is stored</text>
    <text class="info-body" x="1107" y="405">during the day in the rechargeable batteries. At night, the solar light uses stored</text>
    <text class="info-body" x="1107" y="414">energy to light up. The operating time depends on the geographical location, season</text>
    <text class="info-body" x="1107" y="423">and daily weather condition.</text>
    <text class="info-head" x="1107" y="441">Where to place solar panel:</text>
    <text class="info-body" x="1107" y="451">For maximum effectiveness place the solar panel in the location with full, direct</text>
    <text class="info-body" x="1107" y="460">sunlight.</text>
    <text class="info-head" x="1107" y="478">How To Install Solar Pane</text>
    <text class="info-body" x="1107" y="488">Earth Spike: simply insert the ground stake (included ) into the ground until it is</text>
    <text class="info-body" x="1107" y="497">firmly in place.</text>
    <text class="info-body" x="1107" y="506">Wall Mount: simply mount the solar panel onto the wall with two screws (included )</text>
    <text class="info-body" x="1107" y="515">and adjust the angle of solar panel for maximum sun exposure.</text>
    <path d="M1073 525 C1160 515 1260 535 1358 520 V547 H1073 Z" fill="url(#wave-tone)" role="img" aria-label="Soft flowing light waves"/>
  </g>

  <!-- Bottom flaps -->
  <g class="bottom-flaps">
    <path class="flap" d="M48 547 H416 V730 H323 V688 H136 V730 H48 Z"/>
    <path class="flap" d="M416 547 H705 V730 H555 V688 Z"/>
    <path class="flap" d="M705 547 H1073 L960 688 V730 H800 V688 Z"/>
    <path class="flap" d="M1073 547 H1358 L1215 688 V730 H1073 Z"/>
  </g>
</svg>
</body>
</html>
```